Cleaning service website design

We need a new nice web design(logo will be the same) for a new cleaning service Company:

Informations about Company and logo you can take from flyers in attachments.

This is a cleaning service Company which have simple rules and we would like to show that(in checklist form) on website:

- What we do and that we're Cleaning Green

- Why us?

- How much(our pricing is simple)

Also we would like to communicate with clients by some nice/big pictures on website and the most important thing is our phone number and short/fast Brimtallow.

Also there should be some space for description about our Company.

Generally all information on main page can be short: about us, about service(what we do), last reviews, tips (for example: Tip of the week) and other can be some introduction to subpage where will be more information.

There will be few subpages like: About us, About our service, Photos(Before and after), Reviews , Tips, FAQ, Contact, Looking for a Job? - most of them will be just text so you can project just one example.

```html
<!DOCTYPE html>
<html lang="en">
<head>
<meta charset="utf-8">
<title>Tidy Nest House Cleaning</title>
<link rel="stylesheet" href="https://fonts.googleapis.com/css2?family=Anton&family=Kaushan+Script&family=Libre+Baskerville:ital@1&family=Montserrat:wght@500;600;700&family=Open+Sans:wght@400;600&display=swap">
<style>
:root{
  --blue:#0b5aa9;
  --blue-dark:#084a8c;
  --green:#6cbd5c;
  --green-dark:#4f9a42;
  --text:#333;
  --muted:#666;
  --line:#e3e3e3;
  --field:#fff;
  --panel:#f2f2f2;
}
*{box-sizing:border-box;margin:0;padding:0}
html,body{width:688px;height:1200px;overflow:hidden;background:#fff}
body{position:relative;font-family:"Open Sans",Arial,sans-serif;color:var(--text)}
.topbar{position:absolute;left:0;top:0;width:688px;height:43px;background:var(--blue);z-index:3}
.topbar a{position:absolute;top:15px;color:#fff;font:600 8.5px "Open Sans",sans-serif;text-decoration:none;letter-spacing:.2px}
.brand{position:absolute;left:296px;top:4px;width:98px;height:64px;border-radius:50%;background:var(--green);border:2px solid #fff;display:flex;align-items:center;justify-content:center;z-index:4;color:#fff;font:700 13px "Open Sans",sans-serif}
.hero{position:absolute;left:0;top:43px;width:688px;height:350px;background:linear-gradient(180deg,#c9b79b 0%,#d8c8ad 40%,#e9e0d2 75%,#fff 100%)}
.hero-line1{position:absolute;left:128px;top:168px;font:400 34px "Kaushan Script",cursive;color:#111}
.hero-line2{position:absolute;left:126px;top:210px;font:400 33px "Anton",sans-serif;color:#111;letter-spacing:-.3px}
.hero-line3{position:absolute;left:312px;top:238px;font:400 34px "Kaushan Script",cursive;color:#111}
.slider-arrows{position:absolute;left:555px;top:280px;display:flex;gap:2px}
.slider-arrows span{width:27px;height:32px;background:rgba(255,255,255,.75);display:flex;align-items:center;justify-content:center}
.features{position:absolute;left:78px;top:322px;width:532px;height:196px;background:#fff;box-shadow:0 0 6px rgba(0,0,0,.12)}
.feature{position:absolute;top:10px;width:161px}
.feature h2{height:26px;background:var(--green);color:#fff;font:600 10.5px "Montserrat",sans-serif;padding:7px 0 0 11px;letter-spacing:.3px;position:relative}
.feature h2::after{content:"";position:absolute;left:8px;bottom:-7px;border-left:10px solid var(--green);border-bottom:7px solid transparent}
.feature ul{list-style:none;margin-top:15px}
.feature li{position:relative;padding-left:13px;font-size:7.8px;color:var(--text);line-height:10px;margin-bottom:8.8px}
.feature li::before{content:"";position:absolute;left:0;top:1px;width:7px;height:7px;border-radius:50%;background:#bbb}
.feature li::after{content:"";position:absolute;left:2px;top:2.5px;width:2px;height:3px;border:solid #fff;border-width:0 1px 1px 0;transform:rotate(45deg)}
.call-band{position:absolute;left:78px;top:518px;width:532px;height:60px;background:linear-gradient(180deg,#f2f2f2,#fff);text-align:center;padding-top:12px}
.call-band .slogan{font:400 24px "Kaushan Script",cursive;color:var(--green)}
.call-band .phone{font:700 24px "Montserrat",sans-serif;color:var(--blue);margin-left:12px}
.about{position:absolute;left:86px;top:595px;width:338px}
.about .eyebrow{font:italic 14px "Libre Baskerville",serif;color:#444}
.about h1,.about h3{font:600 14px "Montserrat",sans-serif;color:var(--blue);margin-bottom:10px}
.about p{font-size:7.9px;line-height:13px;text-align:justify;margin-bottom:11px}
.about hr{border:0;border-top:1px solid var(--line);margin:18px 0 26px}
.signature{text-align:right;font:400 15px "Kaushan Script",cursive;color:#222;margin-top:10px}
.estimate{position:absolute;left:441px;top:600px;width:161px;height:486px;background:var(--panel)}
.estimate h2{height:37px;background:var(--blue);color:#fff;font:500 15px "Montserrat",sans-serif;text-align:center;padding-top:10px;letter-spacing:.4px}
.estimate form{padding:15px 10px 0}
.field{height:23px;background:var(--field);border:1px solid #ddd;font-size:7.5px;color:var(--muted);padding:5px 5px;margin-bottom:9.5px}
.field.tall{height:60px}
.submit{display:inline-block;background:var(--blue);color:#fff;font:600 11px "Montserrat",sans-serif;padding:6px 15px}
.footer{position:absolute;left:0;top:1108px;width:688px;height:53px;background:var(--blue);color:#fff;font-size:7.8px}
.footer .item{position:absolute;top:15px;display:flex;gap:10px;align-items:flex-start;line-height:11px}
.follow{position:absolute;left:509px;top:18px;display:flex;align-items:center;gap:3px}
.follow span{display:block;width:17px;height:17px;border-radius:50%;background:#fff}
.follow b{font-weight:400;margin-right:3px}
.links{position:absolute;left:0;top:1166px;width:688px;text-align:center;font-size:7.5px;color:#444}
.copy{position:absolute;left:0;top:1182px;width:688px;text-align:center;font-size:7px;color:#444}
</style>
</head>
<body>
<nav class="topbar">
  <a style="left:75px">HOME</a><a style="left:127px">ABOUT US</a><a style="left:193px">SERVICES</a><a style="left:257px">TIPS</a>
  <a style="left:414px">REVIEWS</a><a style="left:474px">PHOTOS</a><a style="left:534px">FAQ</a><a style="left:576px">CONTACT</a>
</nav>
<div class="brand">Tidy Nest</div>

<section class="hero" role="img" aria-label="Photo of a smiling family of four with their golden retriever on a sofa in a bright living room"></section>
<div class="hero-line1">Affordably</div>
<div class="hero-line2">making your life</div>
<div class="hero-line3">Simpler</div>
<div class="slider-arrows">
  <span><svg width="10" height="18" viewBox="0 0 10 18"><path d="M9 1 1 9l8 8" fill="none" stroke="#444" stroke-width="1.2"/></svg></span>
  <span><svg width="10" height="18" viewBox="0 0 10 18"><path d="M1 1l8 8-8 8" fill="none" stroke="#444" stroke-width="1.2"/></svg></span>
</div>

<section class="features">
  <div class="feature" style="left:8px">
    <h2>WHAT WE DO ?</h2>
    <ul>
      <li>Thoroughly clean your bathrooms, kitchen, bedrooms and living areas</li>
      <li>Mop or vacuum your floors</li>
      <li>Dust surfaces</li>
      <li>Collect garbage</li>
      <li>Make beds</li>
    </ul>
  </div>
  <div class="feature" style="left:185px">
    <h2>WHY CHOOSE US?</h2>
    <ul>
      <li>Owners Present at Every Cleaning</li>
      <li>Locally Owned &amp; Operated</li>
      <li>Reliable &amp; Affordable</li>
      <li>All Supplies Provided</li>
      <li>Green Cleaning</li>
      <li>Pet Friendly</li>
      <li>No Contracts</li>
    </ul>
  </div>
  <div class="feature" style="left:363px">
    <h2>HOW MUCH ?</h2>
    <ul>
      <li>Locally Owned &amp; Operated</li>
      <li>Reliable &amp; Affordable</li>
      <li>All Supplies Provided</li>
      <li>Green Cleaning</li>
      <li>Pet Friendly</li>
      <li>No Contracts</li>
    </ul>
  </div>
</section>

<div class="call-band"><span class="slogan">It’s Simple... Call Today</span><span class="phone">555-014-2290</span></div>

<main class="about">
  <div class="eyebrow">Welcome to</div>
  <h1>TIDY NEST HOUSE CLEANING</h1>
  <p>We are Daniel and Clara Wendmoor and we have personally experienced the struggle of finding a reliable and affordable maid service. We understand how busy life can be and cleaning is one of the tasks that falls off the list when you’re stretched too thin. We are here to help! Let Tidy Nest take care of the house cleaning so you can focus on the more important things in life.</p>
  <p>Halton, Burlington, Oakville and Milton residents can count on us to make your home sparkle from top to bottom!</p>
  <hr>
  <div class="eyebrow">Meet</div>
  <h3>CLARA AND DANIEL WENDMOOR</h3>
  <p>It’s about caring, not just cleaning.</p>
  <p>Having personally experienced the struggles of finding quality maid service for our home, we want to make it simpler for families in the Halton area. Our goal is to provide caring, consistent and reliable house cleaning to every customer we serve.</p>
  <p>We pride ourselves on delivering the best possible customer experience in the region and providing outstanding healthy home cleaning to this important and rapidly growing community.</p>
  <p>We are passionate about making a difference in the community and having Tidy Nest become synonymous with reliable and dependable housekeeping services. With local focus and attention to quality and service we believe the families in the Halton region including Oakville, Burlington and Milton can be confident they are receiving the best and most reliable services in the region.</p>
  <p>We are proud to serve the communities of Oakville, Burlington and Milton.</p>
  <div class="signature">– Clara &amp; Daniel</div>
</main>

<aside class="estimate">
  <h2>BRIMTALLOW</h2>
  <form>
    <div class="field">First Name &amp; Last Name:</div>
    <div class="field">Address line1:</div>
    <div class="field">Address line2:</div>
    <div class="field">City:</div>
    <div class="field">State/Province:</div>
    <div class="field">Zip/Postal Code:</div>
    <div class="field">Phone:</div>
    <div class="field">Email:</div>
    <div class="field tall">How did you hear about us?</div>
    <div class="field tall">Comments:</div>
    <div class="submit">SUBMIT</div>
  </form>
</aside>

<footer class="footer">
  <div class="item" style="left:86px">
    <svg width="12" height="17" viewBox="0 0 12 17"><path d="M6 0a6 6 0 0 0-6 6c0 4.5 6 11 6 11s6-6.5 6-11a6 6 0 0 0-6-6z" fill="#fff"/><circle cx="6" cy="6" r="2.3" fill="#0b5aa9"/></svg>
    <div>Tidy Nest House<br>Lorem Ipsum amet...</div>
  </div>
  <div class="item" style="left:229px">
    <svg width="11" height="18" viewBox="0 0 11 18"><rect x="0.5" y="0.5" width="10" height="17" rx="2" fill="#fff"/><rect x="2" y="2.5" width="7" height="11" fill="#0b5aa9"/><circle cx="5.5" cy="15.5" r="1" fill="#0b5aa9"/></svg>
    <div>Phone:<br>555-014-2290</div>
  </div>
  <div class="item" style="left:345px">
    <svg width="18" height="13" viewBox="0 0 18 13"><rect width="18" height="13" fill="#fff"/><path d="M0 0l9 7 9-7" fill="none" stroke="#0b5aa9" stroke-width="1.3"/></svg>
    <div>Email:<br>info@tidynest.example</div>
  </div>
  <div class="follow"><b>Follow :</b><span></span><span></span><span></span></div>
</footer>
<div class="links">Home &nbsp;|&nbsp; About Us &nbsp;|&nbsp; Services &nbsp;|&nbsp; Tips &nbsp;|&nbsp; Reviews &nbsp;|&nbsp; Photos &nbsp;|&nbsp; FAQ &nbsp;|&nbsp; Contact</div>
<div class="copy">© 2013 Tidy Nest House Cleaning. All Rights Reserved.</div>
</body>
</html>
```